Brookvane Consulting Business Card Design

Business Card Design for Brookvane Consulting. Brookvane Consulting is a boutique consultancy based in Atlanta, GA., that specializes in marketing strategy, organization planning, and leadership development. We provide solutions for small businesses and startups as well as Vantage 300 companies.

http://brookvaneconsulting.com/

Target Market(s)

We provide solutions for small businesses and startups as well as Vantage 300 companies.

Industry/Entity Type

Consulting

Contact Information for Business Card

Two sided business card with priority on contact information, logo, tag line (Inspiration to Dream More, Do More, Become More)

Colors

Designer to choose colors to be used in the design.

Requirements
Must have
• contact information, logo, tag line (Inspiration to Dream More, Do More, Become More)
• Simple no over communication.
Nice to have
• I would like to see different placements of logo and creative use of both sides of the card
Should not have
• Do not put too much information on the card.

```html
<!DOCTYPE html>
<html lang="en">
<head>
<meta charset="utf-8">
<title>Brookvane Consulting Business Card</title>
<link href="https://fonts.googleapis.com/css2?family=Open+Sans:wght@400;600&family=Roboto+Condensed:wght@500&display=swap" rel="stylesheet">
<style>
  :root {
    --backdrop: #2b2b2b;
    --card-dark: #1f2021;
    --card-light: #b0b0b0;
    --edge-strip: #a9a9a9;
    --edge-line: #e6e6e6;
    --ink-light: #f2f2f2;
    --ink-muted: #a8a8a8;
    --ink-dark: #111111;
    --divider: #555555;
  }
  * { margin: 0; padding: 0; box-sizing: border-box; }
  html, body { width: 1200px; height: 960px; overflow: hidden; }
  body { background: var(--backdrop); position: relative; font-family: "Open Sans", sans-serif; }

  .card { position: absolute; width: 600px; }
  .card-front {
    left: 314px; top: 113px; height: 343px;
    background: var(--card-dark);
  }
  .card-front .edge {
    position: absolute; left: 0; right: 0; top: 327px; height: 16px;
    background: var(--edge-strip);
    border-top: 3px solid var(--edge-line);
  }
  .front-brand {
    position: absolute; left: 46px; top: 155px; width: 240px;
    color: var(--ink-light); font-weight: 600; font-size: 22px; line-height: 1.2;
  }
  .front-divider {
    position: absolute; left: 288px; top: 115px; width: 1px; height: 127px;
    background: var(--divider);
  }
  .contact { position: absolute; left: 316px; top: 120px; color: var(--ink-light); }
  .contact-name {
    font-family: "Roboto Condensed", sans-serif; font-weight: 500;
    font-size: 20px; color: var(--ink-muted); letter-spacing: 0.2px; line-height: 26px;
  }
  .contact-role { font-size: 15px; font-weight: 600; line-height: 20px; margin-bottom: 10px; }
  .contact-list { list-style: none; }
  .contact-list li { display: flex; align-items: center; font-size: 14px; line-height: 19.5px; }
  .contact-list svg { width: 13px; height: 13px; margin-right: 9px; fill: var(--ink-muted); }

  .card-back {
    left: 311px; top: 472px; height: 342px;
    background: var(--card-light);
  }
  .back-brand {
    position: absolute; left: 0; right: 0; top: 120px; text-align: center;
    color: var(--ink-dark); font-weight: 600; font-size: 36px;
  }
  .tagline {
    position: absolute; left: 0; right: 0; top: 280px; text-align: center;
    color: var(--ink-dark); font-size: 14px;
  }
</style>
</head>
<body>
  <section class="card card-front">
    <div class="front-brand">Brookvane Consulting</div>
    <div class="front-divider"></div>
    <div class="contact">
      <div class="contact-name">DARNELL WHITAKER</div>
      <div class="contact-role">Founder/Managing Director</div>
      <ul class="contact-list">
        <li><svg viewBox="0 0 16 16"><path d="M3.5 1l2.5 3-1.5 2c1 2 3 4 5 5l2-1.5 3 2.5-1.5 2.5C7 14 2 9 1 2.5z"/></svg>424-555-0142</li>
        <li><svg viewBox="0 0 16 16"><path d="M1 3h14v10H1z M2 4l6 5 6-5" stroke="#1f2021" stroke-width="1"/></svg>darnell@brookvaneconsulting.com</li>
        <li><svg viewBox="0 0 16 16"><circle cx="8" cy="8" r="7"/><path d="M1 8h14M8 1c-3 4-3 10 0 14M8 1c3 4 3 10 0 14" stroke="#1f2021" stroke-width="1" fill="none"/></svg>brookvaneconsulting.com</li>
      </ul>
    </div>
    <div class="edge"></div>
  </section>

  <section class="card card-back">
    <div class="back-brand">Brookvane Consulting</div>
    <p class="tagline">Inspiration to Dream More, Do More, Become More</p>
  </section>
</body>
</html>
```